KRT Info Brochure

We need a brochure design for a new not-for-profit organisation that is aimed at providing homeless people with a residence that also provides counselling and vocational training to assist them to find suitable employment at the end of the program.
PLEASE NOTE:
Brochure to be A4.
I know the brochure is quite long, it is really a booklet, but please note that it does not have to have a lot of work done on it, I just want it to look professional and the front cover and inside page to look good.
Also please leave about 2-3 pages at the end as I will be adding in some architect drawings.
Please add in a last page with Contact written at the bottom - we will fill that in later. So please ensure it is editable in PDF.
Thank you so much.
Cheers
Marta

```html
<!DOCTYPE html>
<html lang="en">
<head>
<meta charset="utf-8">
<title>KRT Info Brochure – Spread</title>
<link href="https://fonts.googleapis.com/css2?family=Arimo:wght@400;700&display=swap" rel="stylesheet">
<style>
  :root{
    --backdrop:#e8e8e8;
    --paper:#ffffff;
    --olive:#8f8d3a;
    --olive-dark:#76742c;
    --gold:#f2b632;
    --gold-soft:#f7d27a;
    --heading:#b4982a;
    --ink:#3a3a3a;
    --photo-park:#8c8a7c;
    --photo-shadow:#5f6670;
    --photo-suit:#6b6e74;
  }
  *{box-sizing:border-box;margin:0;padding:0}
  html,body{width:1200px;height:847px;overflow:hidden}
  body{background:var(--backdrop);font-family:"Arimo",Arial,sans-serif;color:var(--ink)}
  .spread{position:absolute;left:40px;top:27px;width:1120px;height:792px;display:flex;box-shadow:0 6px 24px rgba(0,0,0,.18)}
  .page{position:relative;width:560px;height:792px;background:var(--paper);overflow:hidden}
  .page--left{box-shadow:inset -14px 0 18px -14px rgba(0,0,0,.18)}
  .page--right{box-shadow:inset 14px 0 18px -14px rgba(0,0,0,.18)}
  .band{position:absolute;left:0;width:560px}
  .band--top{top:0;height:78px}
  .band--bottom{bottom:0;height:96px}
  .band svg{display:block;width:100%;height:100%}
  .site-url{position:absolute;color:#fff;font-size:10px;letter-spacing:.2px}
  .site-url--top{left:22px;top:18px}
  .site-url--bottom{left:22px;bottom:22px}
  .content{position:absolute;left:26px;right:26px;top:86px}
  h2{color:var(--heading);font-weight:700;font-size:15px;margin:0 0 3px}
  h3{color:var(--heading);font-weight:700;font-size:13px;margin:12px 0 3px}
  p{font-size:10px;line-height:1.32;margin:0 0 8px;text-align:left}
  .photo{display:block}
  .photo--bench{float:right;width:232px;height:104px;margin:0 0 8px 12px;background:linear-gradient(160deg,#b9b6a6,var(--photo-park) 60%,#6f6d62)}
  .photo--alone{float:left;width:196px;height:126px;margin:4px 14px 8px 0;background:radial-gradient(ellipse at 70% 30%,#e9e6dc,#9a9a96 45%,var(--photo-shadow))}
  .photo--advisor{position:absolute;left:350px;top:470px;width:176px;height:218px;background:linear-gradient(180deg,#e6e2da 0,#c9c4ba 30%,var(--photo-suit) 55%,#2f3136);z-index:2}
  .ops{width:322px;clear:both;padding-top:6px}
  .brand{display:flex;align-items:center;justify-content:center;gap:10px;margin-top:22px}
  .brand__rule{width:180px;height:1px;background:var(--olive)}
  .brand__mark{display:flex;align-items:center;gap:5px}
  .brand__dot{width:14px;height:14px;border-radius:50%;background:var(--gold)}
  .brand__name{font-weight:700;font-size:16px;color:var(--olive);line-height:1}
  .closing-rule{width:300px;height:1px;background:var(--olive);margin:46px auto 0}
</style>
</head>
<body>
<main class="spread">
  <section class="page page--left">
    <div class="band band--top">
      <svg viewBox="0 0 560 78" preserveAspectRatio="none" aria-hidden="true">
        <path d="M0 0H560V40C420 70 260 30 120 50 70 57 30 62 0 58Z" fill="var(--olive)"/>
        <path d="M0 58C30 62 70 57 120 50 260 30 420 70 560 40V46C420 76 260 38 120 57 70 64 30 68 0 64Z" fill="var(--gold)"/>
      </svg>
      <span class="site-url site-url--top">www.KRTfoundation.org</span>
    </div>

    <div class="content">
      <div class="photo photo--bench" role="img" aria-label="Photo of an older man lying on a park bench"></div>
      <h2>2.10.Older People</h2>
      <p>KRT will also cater for older people, recognizing the increasingly trend toward homeless in this sector of the population. KRT aims to restore integrity to the Resident by treating them in a respectful and courteous manner, whilst providing them with the counselling to address the issues that made them homeless in the first instance and providing the skills necessary to be placed in appropriate housing and contribute to their own income where possible. Older People's programs will differ from the other programs, in that finding meaningful employment at the completion of the program may not be feasible.</p>
      <p>KRT will provide skills training to enhance existing skills, or teach new skills, whereby Older People could contribute by making/creating items for sale through the KRT shop or online. Furthermore, KRT's Greys (see Complimentary Businesses) will also provide part time employment for this age group. Overall, the main aim for older people is to find them appropriate housing, assist them to obtain appropriate welfare benefits and treat them with integrity and respect.</p>

      <div class="photo photo--alone" role="img" aria-label="Photo of a lone figure sitting against a wall in a bright empty room"></div>
      <h2>2.11.Alcohol &amp; Drug Dependencies</h2>
      <p>If a person is deemed to be homeless and an addict, KRT will work with Alcohol and Drug dependency facility to put the Resident through a drug and/or alcohol rehabilitation program prior to taking up residency at the KRT complex. Once a Resident has been deemed as 'clean' and ready to leave the alcohol/drug facility, the Resident will be admitted to the KRT facility. Alcohol/drug outpatient program will be catered for.</p>

      <div class="ops">
        <h2>3. Operations</h2>
        <p>KRT plans to establish a live-in facility that provides homeless people of all age/groupings to obtain the necessary life skills, training and abilities to obtain appropriate housing, employment and / or the relevant welfare assistance. KRT will provide a specialised program tailored to each individual that is aimed at addressing the initial causes of homelessness through extensive counselling. At the same time KRT will assist the individual to obtain the relevant skills and abilities to move back into society and provide for themselves (and their families, where relevant). Where full-time employment is not an option, KRT will provide the necessary support to obtain the appropriate welfare assistance and/or part time employment.</p>
      </div>
    </div>

    <div class="photo photo--advisor" role="img" aria-label="Photo of a smiling businessman in a suit with arms folded"></div>

    <div class="band band--bottom">
      <svg viewBox="0 0 560 96" preserveAspectRatio="none" aria-hidden="true">
        <path d="M0 40C120 20 260 62 400 42 470 32 520 26 560 30V36C520 32 470 38 400 48 260 68 120 26 0 46Z" fill="var(--gold)"/>
        <path d="M0 46C120 26 260 68 400 48 470 38 520 32 560 36V96H0Z" fill="var(--olive)"/>
      </svg>
    </div>
  </section>

  <section class="page page--right">
    <div class="band band--top">
      <svg viewBox="0 0 560 78" preserveAspectRatio="none" aria-hidden="true">
        <path d="M0 0H560V52C500 60 440 58 380 48 260 30 120 66 0 40Z" fill="var(--olive)"/>
        <path d="M0 40C120 66 260 30 380 48 440 58 500 60 560 52V58C500 66 440 64 380 54 260 36 120 72 0 46Z" fill="var(--gold)"/>
      </svg>
    </div>

    <div class="content">
      <p>In addition, the KRT complex will be environmentally friendly and self-sustaining, which will reduce the overall environmental footprint of the complex and at the same time, reduce on-going costs. Additionally, KRT plans to apply to Open Build Australia to follow the development of the project. This will provide an incredible marketing opportunity, as well as enabling opportunities to local businesses to provide their services at a reduced cost, whilst promoting their businesses.</p>

      <h3>3.1. Management</h3>
      <p>There will be a KRT Management Committee who will oversee the Foundation. The Management Committee will be made up of seven individuals elected bi-annually and the CEO/Founder will act as the Management Committee President. The Committee will be selected from a wide range of experienced individuals with skills ranging from law, finance and psychology.</p>

      <h3>3.2. Business Location</h3>
      <p>The initial KRT facility will be located in the Sunshine Coast Hinterland (approx. 90kms from Brisbane). This location has been chosen as Queensland, the ACT and the Northern Territory have the highest population of homeless people. Given the central location and affordability of property it has been deemed that South East Queensland is the optimal location.</p>
      <p>The facility will be located on large rural acreage that will enable the implementation of all five phases of the supplemental businesses within the Sunshine Coast tourist belt. The location is also optimal for the peace and solitude required for the Residents whilst they heal emotionally and psychologically.</p>
      <p>Furthermore, the location is ideally located to take advantage of the local job market in the Sunshine Coast and Brisbane for Residents at the completion of the Program.</p>
      <p>Residents will be accepted from all over Australia. Residents will be flown from their location to the KRT complex and returned to their original location if required. Aftercare assistance will be provided to Clients regardless of their location.</p>

      <h3>3.3. Foundation Management</h3>
      <p>Marta Hollis is the founder/Chief Executive Officer of the KRT foundation. Marta has a Bachelor of Business / Bachelor of Arts as well as extensive experience working in youth job counselling and vocational training and has 20+ years in senior management experience.</p>

      <div class="brand">
        <span class="brand__rule"></span>
        <span class="brand__mark"><span class="brand__dot"></span><span class="brand__name">KRT</span></span>
        <span class="brand__rule"></span>
      </div>
      <div class="closing-rule"></div>
    </div>

    <div class="band band--bottom">
      <svg viewBox="0 0 560 96" preserveAspectRatio="none" aria-hidden="true">
        <path d="M0 30C60 26 120 34 180 44 320 66 440 22 560 40V46C440 28 320 72 180 50 120 40 60 32 0 36Z" fill="var(--gold)"/>
        <path d="M0 36C60 32 120 40 180 50 320 72 440 28 560 46V96H0Z" fill="var(--olive)"/>
      </svg>
      <span class="site-url site-url--bottom">www.KRTfoundation.org</span>
    </div>
  </section>
</main>
</body>
</html>
```